Create a business promotion flyer to leave in customer mailboxes. We are a bulk petroleum supplier, servicing any industry that requires diesel. Base in griffith NSW, servicing griffith area and surrounds.

Business Name - Terra Diesel
Fuel@terradiesel-example.com.au
Owen - 0491 570 362 ohartley@terradiesel-example.com.au
Liam - 0491 570 718 lprosser@terradiesel-example.com.au
Simon - 0491 570 905 skenway@terradiesel-example.com.au
Office 02 5550 1734

Bulk Fuel deliveries.
Oils & lubricants
Local Family owned business

```html
<!DOCTYPE html>
<html lang="en">
<head>
<meta charset="utf-8">
<title>Terra Diesel – Bulk Fuel Deliveries</title>
<link href="https://fonts.googleapis.com/css2?family=Montserrat:wght@500;600;700&family=Oswald:wght@600;700&display=swap" rel="stylesheet">
<style>
  :root{
    --red:#e31e24;
    --dark:#2f2f31;
    --ink:#1f1f21;
    --text:#2b2b2b;
    --rule:#d6d6d6;
    --white:#ffffff;
    --sky:#3f7fc4;
    --sky-light:#cfe1f2;
    --ground:#b9b6ae;
  }
  *{margin:0;padding:0;box-sizing:border-box}
  html,body{width:800px;height:1200px;overflow:hidden;background:var(--white)}
  .flyer{position:relative;width:800px;height:1200px;overflow:hidden;background:var(--white);font-family:"Montserrat",sans-serif;color:var(--text)}
  .layer{position:absolute;left:0;top:0}
  .brand{position:absolute;left:0;top:96px;width:800px;display:flex;justify-content:center;align-items:center;gap:14px}
  .brand-mark{width:26px;height:26px;background:var(--red)}
  .brand-name{font-family:"Montserrat",sans-serif;font-weight:700;font-size:62px;color:var(--red);letter-spacing:-1px;line-height:1}
  .headline{position:absolute;left:0;width:800px;text-align:center;font-family:"Oswald",sans-serif;font-weight:700;text-transform:uppercase;line-height:1}
  .headline-main{top:196px;font-size:58px;color:var(--ink);letter-spacing:.5px}
  .headline-sub{top:260px;font-size:44px;color:var(--red);letter-spacing:.5px}
  .intro{position:absolute;left:41px;top:640px;width:380px;border-left:2px solid var(--red);padding-left:20px;font-size:13.6px;line-height:21.6px;font-weight:500;color:var(--text)}
  .services{position:absolute;left:30px;top:786px;width:740px;height:224px;display:flex}
  .service{flex:1;display:flex;flex-direction:column;align-items:center;text-align:center}
  .service + .service{border-left:1px solid var(--rule)}
  .service-icon{width:82px;height:82px}
  .service-title{margin-top:20px;font-size:17px;font-weight:700;color:var(--ink);line-height:20px;text-transform:uppercase}
  .service-dash{width:30px;height:2px;background:var(--red);margin:12px 0 16px}
  .service-text{font-size:12px;line-height:17px;font-weight:500;width:170px;color:var(--text)}
  .contacts-rule{position:absolute;left:45px;top:1026px;width:700px;height:1.5px;background:var(--red)}
  .contacts{position:absolute;left:48px;top:1042px;width:720px;height:90px;display:flex}
  .contact{padding-left:0}
  .contact + .contact{border-left:1px solid var(--rule);padding-left:24px}
  .contact-office{width:204px}
  .contact-person{width:172px}
  .contact-name{font-size:16px;font-weight:700;color:var(--red);text-transform:uppercase;line-height:18px}
  .contact-row{display:flex;align-items:flex-start;gap:8px;margin-top:8px}
  .contact-row svg{flex:none;width:24px;height:24px}
  .contact-phone{font-size:15px;font-weight:500;color:var(--ink);line-height:24px}
  .contact-office .contact-phone{font-size:16px}
  .contact-email{font-size:11.5px;font-weight:500;color:var(--ink);line-height:13.5px;padding-top:1px}
  .footer{position:absolute;left:0;top:1155px;width:800px;height:45px;background:var(--dark);display:flex;align-items:center;justify-content:center;gap:10px;color:var(--white);font-size:14px;font-weight:700;letter-spacing:.4px}
  .footer-dot{width:6px;height:6px;border-radius:50%;background:var(--red);margin:0 4px}
</style>
</head>
<body>
<div class="flyer">

  <svg class="layer" width="800" height="1200" viewBox="0 0 800 1200">
    <defs>
      <linearGradient id="sky" x1="0" y1="0" x2="0" y2="1">
        <stop offset="0" stop-color="var(--sky-light)"/>
        <stop offset=".32" stop-color="var(--sky)"/>
        <stop offset=".5" stop-color="#9fb3c6"/>
        <stop offset=".72" stop-color="#d4d8dc"/>
        <stop offset="1" stop-color="var(--ground)"/>
      </linearGradient>
      <linearGradient id="fade" x1="0" y1="0" x2="0" y2="1">
        <stop offset="0" stop-color="#fff" stop-opacity="1"/>
        <stop offset="1" stop-color="#fff" stop-opacity="0"/>
      </linearGradient>
    </defs>
    <g role="img" aria-label="Photo of a white road-train fuel tanker parked in front of a large steel depot shed under a blue sky">
      <path d="M0,240 H800 V560 Q420,690 0,548 Z" fill="url(#sky)"/>
      <rect x="0" y="240" width="800" height="80" fill="url(#fade)"/>
    </g>
    <path d="M0,0 H290 Q120,40 0,150 Z" fill="var(--dark)"/>
    <path d="M0,150 Q120,40 290,0 H300 Q130,50 0,175 Z" fill="var(--red)"/>
    <path d="M415,730 Q640,700 800,572 V650 Q650,720 415,730 Z" fill="var(--red)"/>
    <path d="M420,735 Q660,720 800,672 V742 Q640,742 420,735 Z" fill="var(--dark)"/>
  </svg>

  <div class="brand">
    <span class="brand-mark"></span>
    <span class="brand-name">Terra Diesel</span>
  </div>

  <h1 class="headline headline-main">Powering your business</h1>
  <h2 class="headline headline-sub">With reliable bulk fuel deliveries.</h2>

  <p class="intro">Terra Diesel is a trusted, local, family-owned business specialising in bulk diesel supply for all industries. Based in Griffith NSW, we proudly service Griffith and surrounding areas with reliable, on-time deliveries and personalised customer service you can count on.</p>

  <section class="services">
    <div class="service">
      <svg class="service-icon" viewBox="0 0 82 82" aria-hidden="true">
        <circle cx="41" cy="41" r="39.5" fill="none" stroke="var(--red)" stroke-width="2.5"/>
        <rect x="26" y="22" width="22" height="36" rx="2" fill="var(--red)"/>
        <rect x="30" y="27" width="14" height="9" fill="#fff"/>
        <rect x="23" y="56" width="28" height="5" fill="var(--red)"/>
        <path d="M48,30 L54,35 V52 Q54,56 57,56 Q60,56 60,52 V36 L55,30" fill="none" stroke="var(--red)" stroke-width="2.5" stroke-linejoin="round"/>
      </svg>
      <h3 class="service-title">Bulk fuel<br>deliveries</h3>
      <span class="service-dash"></span>
      <p class="service-text">High-quality diesel delivered safely, reliably and on time.</p>
    </div>
    <div class="service">
      <svg class="service-icon" viewBox="0 0 82 82" aria-hidden="true">
        <circle cx="41" cy="41" r="39.5" fill="none" stroke="var(--red)" stroke-width="2.5"/>
        <path d="M34,18 Q44,32 44,42 A10,10 0 0 1 24,42 Q24,32 34,18 Z" fill="var(--red)"/>
        <g transform="translate(49,48)">
          <circle r="9" fill="none" stroke="var(--red)" stroke-width="5" stroke-dasharray="4 3"/>
          <circle r="6.5" fill="var(--red)"/>
          <circle r="3" fill="#fff"/>
        </g>
      </svg>
      <h3 class="service-title">Oils &amp;<br>lubricants</h3>
      <span class="service-dash"></span>
      <p class="service-text">Premium oils and lubricants to keep your equipment performing at its best.</p>
    </div>
    <div class="service">
      <svg class="service-icon" viewBox="0 0 82 82" aria-hidden="true">
        <circle cx="41" cy="41" r="39.5" fill="none" stroke="var(--red)" stroke-width="2.5"/>
        <g fill="none" stroke="var(--red)" stroke-width="2.2">
          <circle cx="41" cy="26" r="5"/>
          <circle cx="27" cy="30" r="4"/>
          <circle cx="55" cy="30" r="4"/>
          <path d="M19,50 Q19,37 27,37 Q31,37 33,40"/>
          <path d="M63,50 Q63,37 55,37 Q51,37 49,40"/>
          <path d="M31,50 Q31,34 41,34 Q51,34 51,50"/>
        </g>
        <path d="M41,60 L34,53 A4,4 0 0 1 41,47.5 A4,4 0 0 1 48,53 Z" fill="var(--red)"/>
      </svg>
      <h3 class="service-title">Local family<br>owned business</h3>
      <span class="service-dash"></span>
      <p class="service-text">Proudly supporting our local community with honest, dependable service.</p>
    </div>
  </section>

  <div class="contacts-rule"></div>

  <svg width="0" height="0" style="position:absolute">
    <defs>
      <symbol id="icon-phone" viewBox="0 0 24 24">
        <circle cx="12" cy="12" r="12" fill="var(--dark)"/>
        <path d="M8.2,6.5 L10,6.3 L11,9 L9.8,10 Q10.8,12.6 13.6,14 L14.7,12.9 L17.4,14 L17.3,15.8 Q16.8,17.3 15,17.1 Q8.6,16 7,9 Q6.9,7 8.2,6.5 Z" fill="#fff"/>
      </symbol>
      <symbol id="icon-mail" viewBox="0 0 24 24">
        <circle cx="12" cy="12" r="12" fill="var(--dark)"/>
        <rect x="6.5" y="8" width="11" height="8" rx="1" fill="none" stroke="#fff" stroke-width="1.4"/>
        <path d="M6.8,8.5 L12,12.5 L17.2,8.5" fill="none" stroke="#fff" stroke-width="1.4"/>
      </symbol>
    </defs>
  </svg>

  <section class="contacts">
    <div class="contact contact-office">
      <h4 class="contact-name">Office</h4>
      <div class="contact-row"><svg><use href="#icon-phone"/></svg><span class="contact-phone">02 5550 1734</span></div>
      <div class="contact-row"><svg><use href="#icon-mail"/></svg><span class="contact-email">Fuel@terradiesel-<br>example.com.au</span></div>
    </div>
    <div class="contact contact-person">
      <h4 class="contact-name">Owen</h4>
      <div class="contact-row"><svg><use href="#icon-phone"/></svg><span class="contact-phone">0491 570 362</span></div>
      <div class="contact-row"><svg><use href="#icon-mail"/></svg><span class="contact-email">ohartley@<br>terradiesel-<br>example.com.au</span></div>
    </div>
    <div class="contact contact-person">
      <h4 class="contact-name">Liam</h4>
      <div class="contact-row"><svg><use href="#icon-phone"/></svg><span class="contact-phone">0491 570 718</span></div>
      <div class="contact-row"><svg><use href="#icon-mail"/></svg><span class="contact-email">lprosser@<br>terradiesel-<br>example.com.au</span></div>
    </div>
    <div class="contact contact-person">
      <h4 class="contact-name">Simon</h4>
      <div class="contact-row"><svg><use href="#icon-phone"/></svg><span class="contact-phone">0491 570 905</span></div>
      <div class="contact-row"><svg><use href="#icon-mail"/></svg><span class="contact-email">skenway@<br>terradiesel-<br>example.com.au</span></div>
    </div>
  </section>

  <footer class="footer">
    <svg width="18" height="24" viewBox="0 0 18 24" aria-hidden="true">
      <path d="M9,0 A9,9 0 0 1 18,9 Q18,15 9,24 Q0,15 0,9 A9,9 0 0 1 9,0 Z" fill="var(--red)"/>
      <circle cx="9" cy="9" r="3.5" fill="var(--dark)"/>
    </svg>
    <span>PROUDLY BASED IN GRIFFITH NSW</span>
    <span class="footer-dot"></span>
    <span>SERVICING GRIFFITH AND SURROUNDS</span>
  </footer>

</div>
</body>
</html>
```